wealth management firm, professional group, new model

we have a logo that works but we need a card, white background using our colors...clean look

our tag line if can be used in

The Bridge From Client to Owner

```html
<!DOCTYPE html>
<html lang="en">
<head>
<meta charset="utf-8">
<title>Halden Wealth Partners – Business Card</title>
<link rel="stylesheet" href="https://fonts.googleapis.com/css2?family=Montserrat:wght@400;500;700&display=swap">
<style>
  :root {
    --navy: #1b2a4e;
    --ink: #1e2433;
    --paper: #ffffff;
    --backdrop: #b9b9b9;
    --edge: #1b2a4e;
  }
  * { box-sizing: border-box; margin: 0; padding: 0; }
  html, body { width: 1200px; height: 815px; overflow: hidden; }
  body {
    background: var(--backdrop);
    font-family: "Montserrat", sans-serif;
    color: var(--navy);
    display: flex;
    flex-direction: column;
    align-items: center;
    justify-content: center;
    gap: 34px;
  }
  .card {
    position: relative;
    width: 620px;
    height: 354px;
    background: var(--paper);
    border-left: 4px solid var(--edge);
    border-bottom: 4px solid var(--edge);
    box-shadow: 0 10px 24px rgba(0,0,0,0.25);
    overflow: hidden;
  }

  /* Contact side */
  .corner-tab {
    position: absolute;
    top: 0; right: 22px;
    width: 26px; height: 20px;
    background: var(--navy);
    border-radius: 0 0 4px 4px;
  }
  .person {
    position: absolute;
    top: 30px; right: 60px;
    text-align: right;
  }
  .person-name {
    font-weight: 700;
    font-size: 24px;
    letter-spacing: 0.02em;
    color: var(--navy);
  }
  .person-role {
    font-size: 12px;
    color: var(--ink);
    margin-top: 2px;
  }
  .brand-small {
    position: absolute;
    left: 44px; top: 128px;
  }
  .brand-name {
    font-weight: 500;
    color: var(--navy);
    line-height: 1;
  }
  .brand-small .brand-name { font-size: 34px; letter-spacing: 0.42em; }
  .brand-small .brand-sub { font-size: 12px; letter-spacing: 0.22em; margin-top: 6px; }
  .brand-sub { font-weight: 400; color: var(--navy); }
  .contact {
    position: absolute;
    left: 44px; top: 222px;
    font-size: 12.5px;
    color: var(--ink);
    line-height: 1.35;
  }
  .contact-divider {
    width: 14px; height: 1px;
    background: var(--ink);
    margin: 10px 0 9px;
  }
  .contact-list { list-style: none; }
  .contact-list li { display: flex; align-items: center; gap: 7px; }
  .contact-list svg { width: 10px; height: 10px; flex: none; }

  /* Brand side */
  .card-brand {
    display: flex;
    align-items: center;
    justify-content: center;
  }
  .brand-large { text-align: center; }
  .brand-large .brand-name { font-size: 58px; letter-spacing: 0.42em; margin-right: -0.42em; }
  .brand-large .brand-sub { font-size: 20px; letter-spacing: 0.2em; margin-top: 14px; margin-right: -0.2em; }
</style>
</head>
<body>

  <section class="card card-contact" aria-label="Card, contact side">
    <div class="corner-tab"></div>
    <div class="person">
      <div class="person-name">DANIEL REYES</div>
      <div class="person-role">Manager</div>
    </div>

    <div class="brand-small">
      <div class="brand-name">HALDEN</div>
      <div class="brand-sub">WEALTH PARTNERS</div>
    </div>

    <div class="contact">
      <p>Your location street here,<br>Your country name - 9120</p>
      <div class="contact-divider"></div>
      <ul class="contact-list">
        <li>
          <svg viewBox="0 0 10 10" aria-hidden="true"><path d="M2 1l2 2-1 1.2c.6 1.2 1.5 2.1 2.8 2.8L7 6l2 2-1.4 1.4C4.5 9 1 5.5.6 2.4z" fill="var(--navy)"/></svg>
          <span>+012 345 6789</span>
        </li>
        <li>
          <svg viewBox="0 0 10 10" aria-hidden="true"><rect x="0.5" y="2" width="9" height="6.5" fill="var(--navy)"/><path d="M0.5 2L5 5.8 9.5 2" stroke="#fff" stroke-width="0.9" fill="none"/></svg>
          <span>info@youremail.com</span>
        </li>
        <li>
          <svg viewBox="0 0 10 10" aria-hidden="true"><circle cx="5" cy="5" r="4.5" fill="var(--navy)"/><path d="M.5 5h9M5 .5c-2 2.5-2 6.5 0 9M5 .5c2 2.5 2 6.5 0 9" stroke="#fff" stroke-width="0.6" fill="none"/></svg>
          <span>www.yourwebsite.com</span>
        </li>
      </ul>
    </div>
  </section>

  <section class="card card-brand" aria-label="Card, brand side">
    <div class="brand-large">
      <div class="brand-name">HALDEN</div>
      <div class="brand-sub">WEALTH PARTNERS</div>
    </div>
  </section>

</body>
</html>
```